Automotive component supplier needs a business card design

We need a business card design for our company called Velran Global Components Ltd based in the UK. We are a supplier of interior and exterior components to premium car manufacturers such as Corvel Ashby, Hadley Fenn, Marquist and Tavarelli. We would like to see a modern business card design that uses the colour blue.

Target Market(s)

Premium automotive car manufacturers.

Industry/Entity Type

Automotive

Contact Information for Business Card

Company Name : Velran Global Components Limited
Address: 17 Marlow Yard, Upper Heath, Warwick, CV31 8QL, United Kingdom
Web Address : www.velrancomponents-example.co.uk

Font styles to use
Other font styles liked:
• Helvetica

Colors
3176b5
0255a3
85acd3
cfdeed
cee9f5
85cae6
34a6d7
0692cd
9bcb3c

Requirements
Must have
• Clear company logo and a mixture of blue colours.
Nice to have
• A high quality modern image.
Should not have
• Multiple colours.

```html
<!DOCTYPE html>
<html lang="en">
<head>
<meta charset="utf-8">
<title>Velran Global Components – Business Card</title>
<link rel="stylesheet" href="https://fonts.googleapis.com/css2?family=Arimo:wght@400;700&family=Oswald:wght@500;600&display=swap">
<style>
  :root {
    --backdrop: #1c1c1e;
    --blue-deep: #0a7fc4;
    --blue-bright: #1f9ee0;
    --blue-accent: #0692cd;
    --card-white: #ffffff;
    --ink: #1d1d1f;
    --ink-soft: #333333;
  }
  * { margin: 0; padding: 0; box-sizing: border-box; }
  html, body {
    width: 1200px; height: 900px; overflow: hidden;
    background: var(--backdrop);
  }
  .stage {
    width: 1200px; height: 900px;
    display: flex; flex-direction: column;
    align-items: center; justify-content: center; gap: 56px;
  }
  .card {
    width: 560px; height: 320px;
    border-radius: 30px;
    position: relative;
    overflow: hidden;
  }
  /* Front */
  .card-front {
    background: linear-gradient(160deg, var(--blue-deep) 0%, var(--blue-bright) 100%);
    display: flex; align-items: center; justify-content: center;
  }
  .brand-name {
    display: flex; flex-direction: column; line-height: 1;
    color: var(--card-white);
    font-family: "Arimo", Helvetica, Arial, sans-serif;
    font-weight: 700;
  }
  .brand-name .word { font-size: 78px; letter-spacing: 2px; }
  .brand-name .sub { font-size: 19px; letter-spacing: 3.5px; margin-top: 8px; font-weight: 700; }
  /* Back */
  .card-back {
    background: var(--card-white);
    font-family: "Arimo", Helvetica, Arial, sans-serif;
    color: var(--ink);
  }
  .identity {
    position: absolute; left: 24px; top: 110px;
    width: 236px; text-align: right;
    font-family: "Oswald", "Arial Narrow", sans-serif;
    text-transform: uppercase;
    white-space: nowrap;
  }
  .person-name { font-size: 38px; font-weight: 600; line-height: 1; }
  .person-name .surname { color: var(--blue-accent); }
  .person-role { font-size: 19px; font-weight: 500; margin-top: 4px; letter-spacing: .5px; }
  .divider {
    position: absolute; left: 276px; top: 98px;
    width: 1.5px; height: 96px; background: var(--blue-accent);
  }
  .contacts {
    position: absolute; left: 292px; top: 100px;
    list-style: none; font-size: 13px; color: var(--ink-soft);
    white-space: nowrap;
  }
  .contacts li { display: flex; align-items: center; gap: 10px; height: 23px; }
  .contacts svg { width: 13px; height: 13px; flex: none; }
  .contacts .highlight { color: var(--blue-accent); }
  .address {
    position: absolute; left: 0; right: 0; bottom: 42px;
    text-align: center; font-size: 13px; color: var(--ink-soft);
  }
</style>
</head>
<body>
<main class="stage">
  <section class="card card-front" aria-label="Card front">
    <div class="brand-name">
      <span class="word">VELRAN</span>
      <span class="sub">GLOBAL COMPONENTS</span>
    </div>
  </section>

  <section class="card card-back" aria-label="Card back">
    <div class="identity">
      <div class="person-name">Aldric <span class="surname">Penn</span></div>
      <div class="person-role">CEO/Founder</div>
    </div>
    <div class="divider"></div>
    <ul class="contacts">
      <li>
        <svg viewBox="0 0 16 16" aria-hidden="true"><path fill="#0692cd" d="M3.6 1.5l2.3 2.6-1.4 1.7c.9 2 2.4 3.5 4.4 4.4l1.7-1.4 2.6 2.3-1.5 2.3C6.6 13.2 2.8 9.4 1.3 3z"/></svg>
        020-555-0147
      </li>
      <li>
        <svg viewBox="0 0 16 16" aria-hidden="true"><rect x="4" y="1" width="8" height="14" rx="1.5" fill="none" stroke="#0692cd" stroke-width="1.5"/><circle cx="8" cy="12.5" r=".9" fill="#0692cd"/></svg>
        020-555-0193
      </li>
      <li>
        <svg viewBox="0 0 16 16" aria-hidden="true"><rect x="1" y="3" width="14" height="10" fill="#0692cd"/><path d="M1 3l7 6 7-6" fill="none" stroke="#fff" stroke-width="1.2"/></svg>
        aldricpenn@velran-mail.co.uk
      </li>
      <li>
        <svg viewBox="0 0 16 16" aria-hidden="true"><circle cx="8" cy="8" r="7" fill="#0692cd"/><path d="M1 8h14M8 1c-3 3.5-3 10.5 0 14M8 1c3 3.5 3 10.5 0 14" fill="none" stroke="#fff" stroke-width="1"/></svg>
        <span>www.<span class="highlight">velrancomponents-example</span>.co.uk</span>
      </li>
    </ul>
    <p class="address">17 Marlow Yard, Upper Heath, Warwick, CV31 8QL, UK</p>
  </section>
</main>
</body>
</html>
```